Website development company website

ABOUT COMPANY
Hi everyone! We're a Melbourne, Australia website development company in a need of a website design that will make online store merchants want to engage our services.
We specialise exclusively in Torvista e-commerce platform (https://torvista-platform.example/). What distinguishes our business from competition is that rather than designing and building brand new websites, we offer development, support and maintenance services to established websites. Maintenance and Support are the keywords representing our business.
Our potential clients are people with broken, slow and underperforming Torvista installations who need assistance getting their websites up and making sales. Our website must pass the message that we can help, and provide quick means of making contact.
DESIGN
Overall, we're looking for a slick, clean, airy, conservative design. No need to do anything crazy, try to stick to what's "standard" in website design these days and make it easy on all of us. The website is unlikely to be updated too often so it needs to look attractive and fresh first time over and after a year, too.
Attached is our new logo, which you'll be able to take the basic idea from, the colors and fonts. Though, don't use the fonts from the logo in the website, stick to the standard widely supported fonts. Additional use of Google fonts is fine.
Don't overdo it with colors, stick to conservative basic color set and only use the colors from the log for accents like headings etc. Please, don't be tempted to use the blue and orange as background of whole blocks, other than perhaps footer. Thanks.
For the images used, I'd like to stay away from a design studio/digital agency feel and lean more towards professional support and maintenance services. I'm thinking images of content merchants doing their job. Something along the lines of "We'll be taking care of the website so that you only need to care about the business".
Some ideas I like:
http://www.plumframe-pics.example/detail/photo/portrait-of-confident-male-design-professional-royalty-free-image/572048163
http://www.plumframe-pics.example/detail/photo/designer-taking-picture-of-hat-high-res-stock-photography/839207514
http://www.plumframe-pics.example/detail/photo/woman-packaging-pottery-royalty-free-image/216684093
Images of colorful shopping bags and shopping carts are over the top and not serious enough. Instead of images matching Online Shopping, I'd try going more for Stability, Reliability, Performance.
Our existing website is http://www.bravuln.example. Please, don't take design ideas from it, but it will give you a picture of the structure of our new website and content that's going to be used initially.
If you could include a basic icon set to use throughout the website, that would be great. If the icons could match our logo (attached), it would be a big plus.
ALL PAGES
Every page must contain clearly visible phone number (1300 648 907) and a Contact Us Now button, which opens an AJAX driven popup form with Name, Email, Phone and Message to be sent through.
To start with, main menu items will be Torvista, Portfolio, Contact.
At the bottom of each page, please, include a newsletter subscription form with text Subscribe to Torvista Support and Security Updates.
For the footer, I'd like to see a logo strip with the following logos in grayscale (no need to link anywhere): Torvista, QRX, DataVane, NCB. You'll find the logos on Google Images.
Standard footer columns follow. Here, I'd like to see logos in color: Torvista Certified Developer, Torvista Ceritified Solution Provider. Again, the logos are on Google Images.
No social media logos/links necessary anywhere on the website.
...and then the copyright line.
FRONT PAGE
Large slider with images that would appeal to our target audience. Keywords here would be Torvista System Audit, Torvista Performance Optimisation, Torvista Website Emergency Recovery, Torvista Development Infrastructure Hosting. We'll have a static page created for each of these to link to.
In a corner of the slider, or on the edge, can I have an overlay with logos in color (same as footer): Torvista Certified Developer, Torvista Ceritified Solution Provider.
Underneath, a number of blocks, each with an image and teaser that we'll use to link to various pages throughout the website.
PORTFOLIO PAGE
I'm thinking a single long page with a block per client, which will contain project name, description from us and a testimonial from client. Also, each block will contain a single large screenshot. No gallery or slideshow is necessary here, just one image per project.
I'll leave the layout up to you, but try to put yourself in the shoes of a potential client reviewing our past work by simply scrolling down this one page.
CONTACT US PAGE
Separate page with the same form as above, phone number (1300 648 907), email address (support@kavreo.example), address (Suite 42, Level 3|8 Wattlebrook Lane|Fernvale Heights VIC 3999), and a grayscale Google Map.
CODING UP
Coding up into static HTML/CSS/JS is equally important as the design itself. We're a website development company, we'll be integrating the theme. We will spot any issues and we will point them out.
Coded up design must be fully responsive. Enough said.
To be able to create any content in future, we'd like one extra page coded up with samples of all themed elements, lists, forms, buttons, 2, 3, 4-column layout, alerts, icons, etc. This page does not need to be designed, only coded up.
The design will be integrated into Drupal using Twig. If possible at all, try to keep it in mind when designing and coding up, and make the integration into a Drupal theme easier for us.
GOOD LUCK!
That's it. Let me know if anything needs clarifying. So far I've had a great experience with ArtFlockly. I don't doubt some great designs will emerge. Clever ideas are highly appreciated, but also make it clear you've read and followed the points in this brief. Cheers, Tom

```html
<!DOCTYPE html>
<html lang="en">
<head>
<meta charset="utf-8">
<title>Kavreo E-Commerce — Torvista Support &amp; Maintenance</title>
<link rel="stylesheet" href="https://fonts.googleapis.com/css2?family=Ubuntu:wght@400;500;700&family=Open+Sans:wght@400;600;700&display=swap">
<style>
:root{
  --orange:#e8802a;
  --orange-dark:#d9701c;
  --navy:#0d3c70;
  --navy-deep:#07305d;
  --ink:#333b44;
  --text:#5a6068;
  --muted:#8a9097;
  --band:#f3f4f5;
  --line:#e2e4e7;
  --white:#ffffff;
}
*{box-sizing:border-box;margin:0;padding:0}
html,body{width:1200px;height:2514px;overflow:hidden}
body{font-family:"Open Sans",Arial,sans-serif;color:var(--text);background:var(--white);position:relative}

/* Header */
.site-header{position:absolute;top:0;left:0;width:1200px;height:76px;background:var(--white);border-top:4px solid var(--orange);box-shadow:0 1px 4px rgba(0,0,0,.08);z-index:5}
.brand{position:absolute;left:163px;top:16px;display:flex;align-items:center;gap:8px}
.brand-mark{width:20px;height:20px;background:var(--orange)}
.brand-name{font-family:"Ubuntu",sans-serif;font-weight:700;font-size:28px;color:var(--orange);line-height:1}
.main-nav{position:absolute;top:30px;left:404px}
.main-nav a{font-family:"Ubuntu",sans-serif;font-size:12px;color:#222;text-decoration:none;text-transform:uppercase;position:absolute;white-space:nowrap}
.main-nav a.active{color:var(--navy);font-weight:700}
.header-phone{position:absolute;left:805px;top:16px;display:flex;align-items:center;gap:14px}
.header-phone svg{width:34px;height:34px}
.header-phone .label{font-family:"Ubuntu",sans-serif;font-size:13px;color:var(--navy);display:block}
.header-phone .number{font-family:"Ubuntu",sans-serif;font-size:19px;color:var(--orange);display:block;margin-top:2px}

/* Hero */
.hero{position:absolute;top:76px;left:0;width:1200px;height:514px;overflow:hidden}
.hero-photo{position:absolute;inset:0;background:linear-gradient(100deg,#eef4f8 0%,#dbe8f1 35%,#b9cfe0 60%,#7d9cb8 82%,#5d7f9f 100%)}
.hero-title{position:absolute;left:159px;top:172px;font-family:"Ubuntu",sans-serif;font-weight:400;color:#2f3a45;line-height:1.3}
.hero-title .l1{font-size:28px;display:block}
.hero-title .l2{font-size:34px;display:block}
.cert-badges{position:absolute;left:163px;top:301px;display:flex;gap:8px}
.cert-badge{width:68px;height:121px;background:linear-gradient(#eceef0,#b8bcc1);clip-path:polygon(50% 0,100% 18%,100% 100%,0 100%,0 18%)}
.slider-dots{position:absolute;left:1129px;top:232px;display:flex;flex-direction:column;gap:22px}
.slider-dots span{width:12px;height:12px;border-radius:50%;background:#fff}
.slider-dots span.on{background:var(--orange)}

/* Services */
.services{position:absolute;top:590px;left:0;width:1200px;height:315px;background:var(--band)}
.service{position:absolute;top:38px;width:220px;text-align:center;transform:translateX(-50%)}
.service-icon{width:84px;height:84px;border-radius:50%;background:var(--navy);margin:0 auto;display:flex;align-items:center;justify-content:center}
.service-icon--accent{background:var(--orange)}
.service-icon svg{width:34px;height:34px}
.service h3{font-family:"Ubuntu",sans-serif;font-weight:400;font-size:14px;color:#3c434b;line-height:21px;margin-top:23px}
.service p{font-size:11.5px;line-height:19px;color:var(--text);margin-top:7px}
.service .more{display:block;margin-top:16px;font-size:10.5px;font-weight:700;color:var(--orange);text-decoration:none;text-transform:uppercase}

/* Shared section headings */
.section-title{font-family:"Ubuntu",sans-serif;font-weight:400;font-size:24px;color:var(--navy);display:flex;align-items:center;gap:10px}
.section-title .mark{width:12px;height:16px;background:var(--orange)}
.copy p{font-size:11.5px;line-height:20px;color:var(--text);margin-bottom:14px}
.btn{display:inline-block;background:var(--orange);color:#fff;font-size:11px;font-weight:700;text-transform:uppercase;text-decoration:none;border-radius:2px;height:38px;line-height:38px;padding:0 16px}

/* Why section */
.why{position:absolute;top:905px;left:0;width:1200px;height:327px;background:var(--white)}
.why .section-title{position:absolute;left:161px;top:40px}
.why .copy{position:absolute;left:161px;top:90px;width:470px}
.why .btn{position:absolute;left:161px;top:250px;width:141px;padding:0;text-align:center}
.why-visual{position:absolute;left:729px;top:17px;width:302px;height:298px;background:radial-gradient(circle at 50% 58%,#f2f2f2 0%,#d5d6d8 45%,#ffffff 72%)}

/* What we do */
.what{position:absolute;top:1232px;left:0;width:1200px;height:307px;overflow:hidden}
.what-photo{position:absolute;inset:0;background:linear-gradient(90deg,#e2883e 0%,#ea8b3a 30%,#e67f2a 60%,#e27c2b 100%)}
.what .section-title{position:absolute;left:0;width:1200px;top:50px;justify-content:center;color:#fff}
.what .section-title .mark{background:#fff}
.what p{position:absolute;left:232px;top:112px;width:736px;text-align:center;color:#fff;font-size:11px;line-height:21px}
.btn-outline{position:absolute;left:545px;top:218px;width:110px;height:40px;line-height:38px;border:1.5px solid #fff;color:#fff;text-align:center;font-size:11px;font-weight:700;text-transform:uppercase;text-decoration:none}

/* Why Torvista */
.why-platform{position:absolute;top:1539px;left:0;width:1200px;height:358px;background:var(--white)}
.platform-visual{position:absolute;left:201px;top:28px;width:335px;height:310px;background:radial-gradient(circle at 45% 55%,#d8403a 0%,#e96a61 30%,#f3f3f3 52%,#ffffff 75%)}
.why-platform .section-title{position:absolute;left:575px;top:48px}
.why-platform .copy{position:absolute;left:575px;top:95px;width:465px}
.why-platform .btn{position:absolute;left:575px;top:258px;width:276px;padding:0;text-align:center}

/* Featured projects */
.featured-projects{position:absolute;top:1897px;left:0;width:1200px;height:319px;background:var(--band)}
.featured-projects .section-title{position:absolute;left:0;width:1200px;top:34px;justify-content:center}
.partner-grid{position:absolute;left:161px;top:91px;display:grid;grid-template-columns:repeat(4,213px);grid-auto-rows:80px;column-gap:8px;row-gap:25px}
.partner{background:#fff;border:1px solid var(--line);display:flex;align-items:center;justify-content:center;font-family:"Ubuntu",sans-serif;font-weight:500;font-size:26px;color:#7a7f85}

/* Footer */
.site-footer{position:absolute;top:2216px;left:0;width:1200px;height:231px;background:var(--navy);border-top:4px solid var(--orange);color:#fff}
.footer-col{position:absolute;top:36px}
.footer-col h4{font-family:"Ubuntu",sans-serif;font-weight:400;font-size:14px;text-transform:uppercase;letter-spacing:.3px;margin-bottom:10px}
.newsletter{left:161px;width:184px}
.newsletter .intro{font-size:10px;font-style:italic;line-height:15px;margin-bottom:10px}
.newsletter .field{display:block;width:184px;height:26px;background:#fff;margin-bottom:6px;font-size:10px;font-style:italic;color:#777;padding-left:8px;line-height:26px}
.newsletter .subscribe{display:inline-block;margin-top:5px;background:var(--orange);color:#fff;font-size:10.5px;font-weight:700;text-transform:uppercase;height:26px;line-height:26px;padding:0 12px;border-radius:2px}
.links{left:411px}
.links ul{list-style:none}
.links li{font-size:11.5px;line-height:19.5px}
.address{left:540px;width:202px}
.address ul{list-style:none}
.address li{font-size:11px;line-height:21px;display:flex;gap:7px;align-items:flex-start}
.address li svg{width:10px;height:12px;flex:none;margin-top:5px}
.footer-map{position:absolute;left:749px;top:38px;width:288px;height:154px;background:linear-gradient(135deg,#e6e6e6,#cfd0d1)}

.footer-bottom{position:absolute;top:2447px;left:0;width:1200px;height:67px;background:var(--navy-deep);color:#fff}
.mini-badges{position:absolute;left:161px;top:14px;display:flex;gap:3px}
.mini-badges span{width:22px;height:40px;background:linear-gradient(#e2e4e6,#a9adb2);clip-path:polygon(50% 0,100% 18%,100% 100%,0 100%,0 18%)}
.copyright{position:absolute;right:258px;top:27px;font-size:11px}
.footer-brand{position:absolute;left:952px;top:22px;font-family:"Ubuntu",sans-serif;font-weight:700;font-size:18px;color:#fff}
</style>
</head>
<body>

<header class="site-header">
  <div class="brand"><span class="brand-mark"></span><span class="brand-name">Kavreo</span></div>
  <nav class="main-nav">
    <a class="active" href="#" style="left:0">Home</a>
    <a href="#" style="left:72px">About Us</a>
    <a href="#" style="left:166px">Portfolio</a>
    <a href="#" style="left:266px">Contact Us</a>
  </nav>
  <div class="header-phone">
    <svg viewBox="0 0 34 34" aria-hidden="true"><circle cx="17" cy="17" r="15.5" fill="none" stroke="#e8802a" stroke-width="2"/><path d="M12 10c1-1 2-1 2.6 0l1.6 2.6c.4.7.2 1.3-.4 1.8l-1 .8c.8 1.8 2.2 3.2 4 4l.8-1c.5-.6 1.1-.8 1.8-.4l2.6 1.6c1 .6 1 1.6 0 2.6l-1 1c-1.3 1.2-4 .8-7.2-2.4S9.7 12.3 11 11z" fill="#e8802a"/></svg>
    <div><span class="label">Call now for more information</span><span class="number">1300 648 907</span></div>
  </div>
</header>

<section class="hero">
  <div class="hero-photo" role="img" aria-label="Photo of two professionals reviewing work together at a desktop computer in a bright office"></div>
  <h1 class="hero-title"><span class="l1">Responsive Design to</span><span class="l2">Drive Mobile sales</span></h1>
  <div class="cert-badges">
    <div class="cert-badge" role="img" aria-label="Torvista Certified Developer badge"></div>
    <div class="cert-badge" role="img" aria-label="Torvista Ceritified Solution Provider badge"></div>
  </div>
  <div class="slider-dots"><span class="on"></span><span></span></div>
</section>

<section class="services">
  <div class="service" style="left:251px">
    <div class="service-icon service-icon--accent"><svg viewBox="0 0 34 34" aria-hidden="true"><rect x="8" y="9" width="18" height="12" rx="1" fill="none" stroke="#fff" stroke-width="2"/><path d="M5 24h24" stroke="#fff" stroke-width="2.4" stroke-linecap="round"/></svg></div>
    <h3>Torvista<br>System Audit</h3>
    <p>Sed ut perspiciatis unlorede nis natus error sit voluptatem accusaum doloremque lauloredantiumto.</p>
    <a class="more" href="#">Click here</a>
  </div>
  <div class="service" style="left:483px">
    <div class="service-icon"><svg viewBox="0 0 34 34" aria-hidden="true"><path d="M27 7L6 16l7 3 2 8 4-5 5 4z" fill="#fff"/><path d="M13 19l14-12" stroke="#0d3c70" stroke-width="1.4"/></svg></div>
    <h3>Torvista<br>Performance Optimisation</h3>
    <p>Sed ut perspiciatis unlorede nis natus error sit voluptatem accusaum doloremque lauloredantiumto.</p>
    <a class="more" href="#">Click here</a>
  </div>
  <div class="service" style="left:712px">
    <div class="service-icon"><svg viewBox="0 0 34 34" aria-hidden="true"><circle cx="17" cy="17" r="10" fill="#fff"/><path d="M12 12c2 0 3 1 3 3s-2 2-2 4 2 2 2 4M20 10c-1 2 1 3 2 4s3 0 3 2" stroke="#0d3c70" stroke-width="1.6" fill="none"/></svg></div>
    <h3>Torvista Website<br>Emergency Recovery</h3>
    <p>Sed ut perspiciatis unlorede nis natus error sit voluptatem accusaum doloremque lauloredantiumto.</p>
    <a class="more" href="#">Click here</a>
  </div>
  <div class="service" style="left:944px">
    <div class="service-icon"><svg viewBox="0 0 34 34" aria-hidden="true"><circle cx="13" cy="19" r="6" fill="none" stroke="#fff" stroke-width="4" stroke-dasharray="3 2.3"/><circle cx="13" cy="19" r="3" fill="#fff"/><circle cx="23" cy="11" r="4" fill="none" stroke="#fff" stroke-width="3" stroke-dasharray="2 1.8"/><circle cx="23" cy="11" r="1.6" fill="#fff"/></svg></div>
    <h3>Torvista Development<br>Infrastructure Hosting</h3>
    <p>Sed ut perspiciatis unlorede nis natus error sit voluptatem accusaum doloremque lauloredantiumto.</p>
    <a class="more" href="#">Click here</a>
  </div>
</section>

<section class="why">
  <h2 class="section-title"><span class="mark"></span>Why Kavreo E- Commerce?</h2>
  <div class="copy">
    <p>Fast Torvista-based online stores, built on time and to specification, backed by effective, focused support, means that our clients are among the happiest in the eCommerce world.</p>
    <p>Sed ut perspiciatis unde omnis iste natus error sit voluptatem accusantium doloremque laudantium, totam rem aperiam, eaque ipsa quae ab illo inventore veritatis et quasi archite cto beatae vitae dicta sunt explicabo.emo enim ipsam voluptatem quiaaspernatur aut odit aut fugit, sed quia consequunt.</p>
  </div>
  <a class="btn" href="#">Contact us now!</a>
  <div class="why-visual" role="img" aria-label="Illustration of a silver stopwatch with a dial marked reliability"></div>
</section>

<section class="what">
  <div class="what-photo" role="img" aria-label="Orange-tinted photo of a smiling woman working at a computer"></div>
  <h2 class="section-title"><span class="mark"></span>What We Do.</h2>
  <p>From support, maintenance and upgrades to redesigns, migrations and full site builds, we make your online store do what you need it to do.Sed ut perspiciatis unde omnis iste natus error sit voluptatem accusantium doloremque laudantium, totam rem aperiam, eaque ipsa quae ab illo inventore veritatis et quasi archite cto beatae vitae dicta sunt explicabo.emoium doloremque laudantium, totam rem aperiam, eaque ipsa quae ab illo inventore veritatis et quasi archite cto beatae vitae dicta sunt explicabo.emo enim ipsam voluptatem quia. aspernatur aut odit</p>
  <a class="btn-outline" href="#">Read more</a>
</section>

<section class="why-platform">
  <div class="platform-visual" role="img" aria-label="Illustration of a red and white target with three arrows in the bullseye"></div>
  <h2 class="section-title"><span class="mark"></span>Why Torvista and Kavreo?</h2>
  <div class="copy">
    <p>Torvista is the world's leading open source eCommerce platform. No other open-source or free system offers out-of-the-box functionality and search engine friendliness comparable to Torvista CE.</p>
    <p>Sed ut perspiciatis unde omnis iste natus error sit voluptatem accusantium doloremque laudantium, totam rem aperiam, eaque ipsa quae ab illo inventore veritatis et quasi archite cto beatae vitae dicta sunt explicabo.emo enim ipsam voluptatem quia.</p>
  </div>
  <a class="btn" href="#">Read more about Torvista &amp; Kavreo</a>
</section>

<section class="featured-projects">
  <h2 class="section-title"><span class="mark"></span>Featured Projects</h2>
  <div class="partner-grid">
    <div class="partner">Torvista</div>
    <div class="partner">QRX</div>
    <div class="partner">DataVane</div>
    <div class="partner">NCB</div>
    <div class="partner">Orvantis</div>
    <div class="partner">Mivrosel</div>
    <div class="partner">Sapphyr</div>
    <div class="partner">Velmora</div>
  </div>
</section>

<footer class="site-footer">
  <div class="footer-col newsletter">
    <h4>Newsletter</h4>
    <p class="intro">Lorem ipsum dolor sit ametconsec tetur adipiscing elit, sed do.</p>
    <span class="field">Name:</span>
    <span class="field">Email:</span>
    <span class="subscribe">Subscribe</span>
  </div>
  <div class="footer-col links">
    <h4>Links</h4>
    <ul><li>Home</li><li>About Us</li><li>Portfolio</li><li>Projects</li><li>Contact Us</li><li>FAQ</li></ul>
  </div>
  <div class="footer-col address">
    <h4>Company Address</h4>
    <ul>
      <li><svg viewBox="0 0 10 12" aria-hidden="true"><path d="M5 0a4 4 0 0 1 4 4c0 3-4 8-4 8S1 7 1 4a4 4 0 0 1 4-4z" fill="#e8802a"/><circle cx="5" cy="4" r="1.5" fill="#0d3c70"/></svg><span>Suite 42, Level 3|8 Wattlebrook Lane| Fernvale Heights VIC 3999</span></li>
      <li><svg viewBox="0 0 10 12" aria-hidden="true"><path d="M2 1c.6-.6 1.2-.6 1.6 0l1 1.6c.2.4 0 .8-.3 1l-.5.5c.5 1.1 1.2 1.9 2.2 2.4l.5-.5c.3-.4.7-.5 1-.3l1.6 1c.6.4.6 1 0 1.6l-.6.6C7.7 10 6 9.7 4.2 7.8S1.3 3.6 2 2.6z" fill="#e8802a"/></svg><span>Phone: (1300 648 907)</span></li>
      <li><svg viewBox="0 0 10 12" aria-hidden="true"><rect x="0" y="3" width="10" height="7" fill="#e8802a"/><path d="M0 3l5 4 5-4" stroke="#0d3c70" stroke-width="1" fill="none"/></svg><span>Email: support@kavreo.example</span></li>
    </ul>
  </div>
  <div class="footer-map" role="img" aria-label="Grayscale street map with an orange pin marking the office location"></div>
</footer>

<div class="footer-bottom">
  <div class="mini-badges" role="img" aria-label="Torvista certification badges"><span></span><span></span></div>
  <p class="copyright">© 2016 All copyrights Reserved. Kavreo E-Commerce</p>
  <span class="footer-brand">Kavreo</span>
</div>

</body>
</html>
```